Computer consultant business card

Bexil Software is a newly started computer consulting company. It's a small one-man company that provides mostly Vornix applications but also websites in collaboration with designers. I'm running this company on the side of full time university studies.

I want the final design to be clean and memorable. Be creative! :)

Some inspiration:
http://www.pixelmarta.com/design/48317
http://www.pixelmarta.com/design/2739164/business-card-design-by-frostlynk
http://www.pixelmarta.com/design/604281/business-card-design-by-koralind-vestrabanu

See attachment for my company logo.
Updates

I would like to thank everyone for submitting! I'll need a couple of days to review and ultimately select a design.

Target Market(s)

Non-technical entrepreneurs and small companies.

Industry/Entity Type

University

Requirements
Must have
• My company logo.
In any way, both colors from my logo.
First- and last name, e-mail and phone number.
Double-sided design.
Nice to have
• Something creative with the symbol in my logo

```html
<!DOCTYPE html>
<html lang="en">
<head>
<meta charset="utf-8">
<title>Bexil Software — Business Card</title>
<link href="https://fonts.googleapis.com/css2?family=Quicksand:wght@500&family=Lora:wght@400&display=swap" rel="stylesheet">
<style>
  :root {
    --backdrop: #e8e5e0;
    --card-white: #f4f4f4;
    --card-white-edge: #e2e2e2;
    --panel-grey: #d5d5d5;
    --rule-white: #fbfbfb;
    --accent-blue: #4a7fc1;
    --accent-blue-dark: #3a68a6;
    --accent-grey: #8e8e8e;
    --accent-black: #121212;
    --logo-grey: #6a6a6b;
    --tagline-grey: #8a8a8a;
  }
  * { box-sizing: border-box; margin: 0; padding: 0; }
  html, body {
    width: 1200px; height: 1023px; overflow: hidden;
    background: var(--backdrop);
  }
  .sheet {
    position: relative; width: 1200px; height: 1023px;
    display: flex; flex-direction: column; align-items: center;
    justify-content: center; gap: 70px;
  }
  .card {
    position: relative; width: 680px; height: 388px;
    background: linear-gradient(180deg, var(--card-white) 0%, var(--card-white-edge) 100%);
    box-shadow: 0 10px 26px rgba(0,0,0,.18);
    overflow: hidden;
  }
  .card__band {
    position: absolute; left: 0; right: 0; top: 96px; height: 196px;
    display: flex; gap: 6px; background: var(--rule-white);
  }
  .card__end { width: 96px; height: 100%; }
  .card__end--blue { background: linear-gradient(180deg, var(--accent-blue), var(--accent-blue-dark)); }
  .card__end--grey { background: linear-gradient(180deg, #9d9d9d, var(--accent-grey)); }
  .card__end--black { background: var(--accent-black); }
  .card__panel {
    flex: 1; height: 100%; background: var(--panel-grey);
    display: flex; align-items: center; justify-content: center;
  }
  .brand { display: flex; align-items: center; gap: 16px; }
  .brand__dot {
    width: 46px; height: 46px; border-radius: 50%;
    background: var(--accent-blue);
  }
  .brand__text { display: flex; flex-direction: column; }
  .brand__name {
    font-family: "Quicksand", sans-serif; font-weight: 500;
    font-size: 64px; line-height: 1; color: var(--logo-grey);
    letter-spacing: 1px;
  }
  .brand__tagline {
    font-family: "Lora", serif; font-size: 12px;
    color: var(--tagline-grey); letter-spacing: .5px; margin-top: 4px;
  }
  .contact {
    width: 100%; padding: 0 48px;
    display: flex; flex-direction: column; gap: 6px;
  }
  .contact__name {
    font-family: "Quicksand", sans-serif; font-weight: 500;
    font-size: 30px; line-height: 1.1; color: var(--logo-grey);
  }
  .contact__role {
    font-family: "Lora", serif; font-size: 13px;
    color: var(--accent-blue-dark); letter-spacing: .5px;
    margin-bottom: 14px;
  }
  .contact__line {
    font-family: "Lora", serif; font-size: 14px;
    color: var(--logo-grey); letter-spacing: .3px;
    display: flex; align-items: center; gap: 10px;
  }
  .contact__icon { width: 14px; height: 14px; flex: none; }
</style>
</head>
<body>
<main class="sheet">
  <section class="card card--front" aria-label="Card front">
    <div class="card__band">
      <div class="card__end card__end--blue"></div>
      <div class="card__panel">
        <div class="brand">
          <span class="brand__dot"></span>
          <div class="brand__text">
            <span class="brand__name">bexil</span>
            <span class="brand__tagline">tagline / slogan / website</span>
          </div>
        </div>
      </div>
      <div class="card__end card__end--grey"></div>
    </div>
  </section>

  <section class="card card--back" aria-label="Card back">
    <div class="card__band">
      <div class="card__end card__end--blue"></div>
      <div class="card__panel">
        <div class="contact">
          <span class="contact__name">Mira Tallen</span>
          <span class="contact__role">Vornix Developer</span>
          <span class="contact__line">
            <svg class="contact__icon" viewBox="0 0 14 14" aria-hidden="true">
              <rect x="1" y="3" width="12" height="8" fill="none" stroke="#4a7fc1" stroke-width="1.4"/>
              <path d="M1 3 L7 8 L13 3" fill="none" stroke="#4a7fc1" stroke-width="1.4"/>
            </svg>
            mira@bexil.se
          </span>
          <span class="contact__line">
            <svg class="contact__icon" viewBox="0 0 14 14" aria-hidden="true">
              <path d="M3 1 L5.5 1 L6.5 4 L5 5.2 C5.8 7 7 8.2 8.8 9 L10 7.5 L13 8.5 L13 11 C13 12 12 13 11 13 C5.5 12.5 1.5 8.5 1 3 C1 2 2 1 3 1 Z" fill="#4a7fc1"/>
            </svg>
            +46 70 412 88 30
          </span>
        </div>
      </div>
      <div class="card__end card__end--black"></div>
    </div>
  </section>
</main>
</body>
</html>
```